Corvel Capital LLC

Need Professional Business cards for New Investment Fund

Target Market(s)

High Quality investors

Industry/Entity Type

Financial

Contact Information for Business Card

Phone Number +1 555 284 6190
Name Lukas Varenko
Title Fund Manager
email lv@FundCorvel.com
Website www.FundCorvel.com

Colors

Designer to choose colors to be used in the design.

Requirements
Must have
• Must have our Logo and all of the above. Must be made so lettering and loge can be raised

```html
<!DOCTYPE html>
<html lang="en">
<head>
<meta charset="utf-8">
<title>Quenvale – Business Card</title>
<link href="https://fonts.googleapis.com/css2?family=Roboto:wght@400;500;700&display=swap" rel="stylesheet">
<style>
  :root {
    --backdrop: #e2e2e2;
    --paper: #ffffff;
    --slate-top: #5a6457;
    --slate-bottom: #434a41;
    --brand-green: #24ec00;
    --brand-dark: #4a5247;
    --text-light: #ffffff;
  }
  html, body {
    margin: 0;
    padding: 0;
    width: 1200px;
    height: 1200px;
    overflow: hidden;
    background: var(--backdrop);
    font-family: "Roboto", sans-serif;
  }
  .canvas {
    position: relative;
    width: 1200px;
    height: 1200px;
  }
  .card {
    position: absolute;
    left: 200px;
    width: 800px;
    height: 457px;
    overflow: hidden;
  }
  .card--front { top: 110px; background: var(--paper); }
  .card--back  { top: 633px; background: var(--brand-green); }
  .card__art {
    position: absolute;
    inset: 0;
  }
  .holder {
    position: absolute;
    left: 38px;
    top: 270px;
  }
  .holder__name {
    margin: 0;
    color: var(--brand-green);
    font-weight: 500;
    font-size: 26px;
    line-height: 1;
  }
  .holder__title {
    margin: 8px 0 0;
    color: var(--text-light);
    font-weight: 500;
    font-size: 18px;
  }
  .contacts {
    list-style: none;
    margin: 0;
    padding: 0;
    position: absolute;
    left: 38px;
    top: 354px;
    color: var(--text-light);
    font-size: 18px;
  }
  .contacts__item {
    display: flex;
    align-items: center;
    height: 23px;
  }
  .contacts__icon {
    width: 15px;
    height: 15px;
    margin-right: 11px;
    fill: var(--brand-green);
  }
  .wordmark {
    position: absolute;
    display: flex;
    align-items: center;
    gap: 12px;
    color: var(--brand-dark);
    font-weight: 500;
    font-size: 40px;
    letter-spacing: 1px;
    white-space: nowrap;
  }
  .wordmark__square {
    width: 24px;
    height: 24px;
    background: var(--brand-dark);
  }
  .card--front .wordmark { left: 610px; top: 178px; transform: translate(-50%, -50%); }
  .card--back .wordmark { left: 50%; top: 50%; transform: translate(-50%, -50%); }
</style>
</head>
<body>
<div class="canvas">

  <section class="card card--front" aria-label="Business card front">
    <svg class="card__art" width="800" height="457" viewBox="0 0 800 457">
      <defs>
        <linearGradient id="slate" x1="0" y1="0" x2="0" y2="1">
          <stop offset="0" stop-color="var(--slate-top)"/>
          <stop offset="1" stop-color="var(--slate-bottom)"/>
        </linearGradient>
      </defs>
      <polygon points="0,0 211,0 443,457 0,457" fill="url(#slate)"/>
      <line x1="236" y1="44" x2="451" y2="457" stroke="var(--brand-green)" stroke-width="5"/>
      <polygon points="229,30 260,53 244,55 238,70" fill="var(--brand-green)"/>
    </svg>

    <div class="holder">
      <h1 class="holder__name">Lukas Varenko</h1>
      <p class="holder__title">Fund Manager</p>
    </div>

    <ul class="contacts">
      <li class="contacts__item">
        <svg class="contacts__icon" viewBox="0 0 24 24"><path d="M6.6 10.8a15.1 15.1 0 0 0 6.6 6.6l2.2-2.2a1 1 0 0 1 1-.25 11.4 11.4 0 0 0 3.6.57 1 1 0 0 1 1 1V20a1 1 0 0 1-1 1A17 17 0 0 1 3 4a1 1 0 0 1 1-1h3.5a1 1 0 0 1 1 1c0 1.25.2 2.45.57 3.57a1 1 0 0 1-.25 1z"/></svg>
        +1 555 284 6190
      </li>
      <li class="contacts__item">
        <svg class="contacts__icon" viewBox="0 0 24 24"><path d="M2 5h20v14H2z M2 6l10 7 10-7" /></svg>
        lv@FundCorvel.com
      </li>
      <li class="contacts__item">
        <svg class="contacts__icon" viewBox="0 0 24 24"><circle cx="12" cy="12" r="10"/></svg>
        www.FundCorvel.com
      </li>
    </ul>

    <div class="wordmark"><span class="wordmark__square"></span>Quenvale</div>
  </section>

  <section class="card card--back" aria-label="Business card back">
    <div class="wordmark"><span class="wordmark__square"></span>Quenvale</div>
  </section>

</div>
</body>
</html>
```